KDWB Business Card

Looking for a business card design to incorporate our branding. We want to only use the colors listing in the Branding Package (attached).
Updates

Target Market(s)

People who need their phone or device fixed.

Industry/Entity Type

Electronics

Contact Information for Business Card

Please use:

Brightwick Gadget Clinic LLC
4810 E Harlow Ridge Rd
Suite 417
San Antonio, TX 78163

Marcus Delgrove, Store Manager

(210) 555-0147

Requirements
Must have
• Must include the colors that are contained within the Branding Package PDF file.

```html
<!DOCTYPE html>
<html lang="en">
<head>
<meta charset="utf-8">
<title>Brightwick Gadget Clinic – Business Card</title>
<link rel="stylesheet" href="https://fonts.googleapis.com/css2?family=Questrial&display=swap">
<style>
  :root {
    --brand-orange: #f05a22;
    --brand-lime: #c9d64a;
    --card-white: #ffffff;
    --pattern-tint: #fbf3ee;
    --ink-grey: #4a4a4a;
    --backdrop: #2a2a2a;
  }
  * { margin: 0; padding: 0; box-sizing: border-box; }
  html, body { width: 1200px; height: 880px; overflow: hidden; }
  body {
    background: var(--backdrop);
    font-family: "Questrial", "Century Gothic", sans-serif;
    position: relative;
  }
  .card {
    position: absolute;
    width: 560px;
    height: 320px;
    background: var(--card-white);
    border-radius: 22px;
    overflow: hidden;
  }
  .card--front { left: 60px; top: 80px; }
  .card--back { left: 580px; top: 480px; }

  /* front */
  .front-pattern {
    position: absolute; inset: 0;
    background: linear-gradient(135deg, var(--pattern-tint), var(--card-white));
  }
  .front-brand {
    position: absolute; inset: 0;
    display: flex; flex-direction: column; align-items: center; justify-content: center;
    gap: 22px;
  }
  .brand-square {
    width: 84px; height: 84px;
    border: 3px solid var(--brand-orange);
    border-radius: 18px;
  }
  .front-name {
    color: var(--brand-orange);
    font-size: 22px;
    letter-spacing: 0.5px;
  }

  /* back */
  .back-brand {
    position: absolute; left: 40px; top: 92px;
    display: flex; align-items: center; gap: 14px;
  }
  .back-brand .brand-square {
    width: 60px; height: 60px;
    background: var(--brand-orange);
    border: none;
    border-radius: 12px;
  }
  .back-name {
    color: var(--brand-orange);
    font-size: 30px;
    line-height: 1;
  }
  .mini-brand {
    position: absolute; right: 30px; top: 30px;
    display: flex; align-items: center; gap: 8px;
  }
  .mini-brand .brand-square {
    width: 24px; height: 24px;
    background: var(--brand-orange);
    border: none; border-radius: 5px;
  }
  .mini-name { color: var(--brand-orange); font-size: 13px; }

  .contact-person {
    position: absolute; left: 40px; bottom: 36px;
  }
  .person-name { color: var(--brand-orange); font-size: 22px; }
  .person-role { color: var(--ink-grey); font-size: 15px; margin-top: 2px; }
  .person-phone {
    display: flex; align-items: center; gap: 8px;
    color: var(--ink-grey); font-size: 15px; margin-top: 10px;
  }
  .phone-icon {
    width: 22px; height: 18px; background: var(--brand-orange); border-radius: 3px;
    display: flex; align-items: center; justify-content: center;
  }
  .address {
    position: absolute; right: 36px; bottom: 36px;
    color: var(--ink-grey); font-size: 15px; line-height: 1.45;
    font-style: normal;
  }
</style>
</head>
<body>
  <section class="card card--front">
    <div class="front-pattern" role="img" aria-label="Faint repeating tile pattern in pale orange"></div>
    <div class="front-brand">
      <div class="brand-square"></div>
      <p class="front-name">Brightwick Gadget Clinic LLC</p>
    </div>
  </section>

  <section class="card card--back">
    <div class="mini-brand">
      <div class="brand-square"></div>
      <span class="mini-name">Brightwick Gadget Clinic</span>
    </div>
    <div class="back-brand">
      <div class="brand-square"></div>
      <span class="back-name">Brightwick Gadget Clinic</span>
    </div>
    <div class="contact-person">
      <p class="person-name">Marcus Delgrove</p>
      <p class="person-role">Store Manager</p>
      <p class="person-phone">
        <span class="phone-icon">
          <svg width="12" height="12" viewBox="0 0 24 24" aria-hidden="true">
            <path fill="#fff" d="M6.6 10.8a15 15 0 0 0 6.6 6.6l2.2-2.2c.3-.3.7-.4 1-.2 1.1.4 2.3.6 3.6.6.6 0 1 .4 1 1V20c0 .6-.4 1-1 1A17 17 0 0 1 3 4c0-.6.4-1 1-1h3.5c.6 0 1 .4 1 1 0 1.3.2 2.5.6 3.6.1.3 0 .7-.2 1z"/>
          </svg>
        </span>
        (210) 555-0147
      </p>
    </div>
    <address class="address">
      4810 E Harlow Ridge Rd<br>
      Suite 417<br>
      San Antonio, TX 78163
    </address>
  </section>
</body>
</html>
```